Business Card Design Project

We are a construction company in Orange County, CA. We need a two sided business card. We would like the back to be our logo with web URL. Front should included Name, title, address, phone, fax and email address.

our address is
627 West Dorrance Blvd, Suite 308
Anaheim, CA 92718

Our logo files are attached.

Construction

```html
<!DOCTYPE html>
<html lang="en">
<head>
<meta charset="utf-8">
<title>Verlan Business Card</title>
<link rel="stylesheet" href="https://fonts.googleapis.com/css2?family=Arimo:wght@400;700&family=Tinos:wght@700&display=swap">
<style>
  :root {
    --brand-blue: #24518a;
    --brand-blue-dark: #1b3f6e;
    --text-blue: #2f6fb5;
    --ink: #1a1a1a;
    --card-white: #ffffff;
    --backdrop: #e9ebee;
  }
  * { box-sizing: border-box; margin: 0; padding: 0; }
  html, body { width: 1200px; height: 900px; overflow: hidden; }
  body {
    background: var(--backdrop);
    font-family: "Arimo", Arial, sans-serif;
    position: relative;
  }
  .card {
    position: absolute;
    width: 620px;
    height: 354px;
    border-radius: 24px;
    box-shadow: 0 10px 26px rgba(0,0,0,0.18);
    overflow: hidden;
  }
  /* Back side */
  .card-back {
    left: 80px;
    top: 70px;
    background: var(--brand-blue);
  }
  .card-back .company-name {
    position: absolute;
    left: 0; right: 0;
    top: 128px;
    text-align: center;
    color: var(--card-white);
    font-weight: 700;
    font-size: 84px;
    letter-spacing: 2px;
    line-height: 1;
  }
  .card-back .web {
    position: absolute;
    right: 34px;
    bottom: 28px;
    color: var(--card-white);
    font-size: 17px;
  }
  /* Front side */
  .card-front {
    left: 500px;
    top: 476px;
    background: var(--card-white);
    border-bottom: 6px solid var(--brand-blue);
  }
  .card-front .company-name {
    position: absolute;
    left: 26px;
    top: 22px;
    color: var(--brand-blue);
    font-weight: 700;
    font-size: 50px;
    letter-spacing: 1px;
    line-height: 1;
  }
  .holder {
    position: absolute;
    left: 70px;
    top: 148px;
  }
  .holder .name {
    font-family: "Tinos", "Times New Roman", serif;
    font-weight: 700;
    font-size: 24px;
    color: var(--text-blue);
  }
  .holder .role {
    font-size: 17px;
    color: var(--ink);
    margin-top: 2px;
  }
  .contact {
    position: absolute;
    left: 372px;
    top: 162px;
    font-size: 15px;
    color: var(--ink);
  }
  .contact .address {
    color: var(--text-blue);
    line-height: 1.15;
    margin-bottom: 10px;
  }
  .contact .line {
    display: flex;
    align-items: center;
    gap: 14px;
    height: 24px;
  }
  .contact svg { width: 16px; height: 16px; flex: none; }
  .web-tab {
    position: absolute;
    right: 58px;
    bottom: 0;
    width: 240px;
    height: 38px;
    background: var(--brand-blue);
    border-radius: 12px 12px 0 0;
    color: var(--card-white);
    font-size: 17px;
    display: flex;
    align-items: center;
    justify-content: center;
  }
</style>
</head>
<body>

  <section class="card card-back" aria-label="Business card back">
    <div class="company-name">VERLAN</div>
    <div class="web">www.verlanbuild.com</div>
  </section>

  <section class="card card-front" aria-label="Business card front">
    <div class="company-name">VERLAN</div>

    <div class="holder">
      <div class="name">Marcus D. Hallett</div>
      <div class="role">Operation Manager</div>
    </div>

    <div class="contact">
      <div class="address">627 West Dorrance Blvd, Suite 308<br>Anaheim, CA 92718</div>
      <div class="line">
        <svg viewBox="0 0 16 16" aria-hidden="true"><path fill="#24518a" d="M3.6 1.2l2.3 2.6-1.3 1.7c.9 2 2.2 3.4 4.3 4.5l1.6-1.3 2.7 2.2-1.4 2.7C6.8 13.2 2.6 9 1.2 3.1z"/></svg>
        <span>(+11) 555 018 2240</span>
      </div>
      <div class="line">
        <svg viewBox="0 0 16 16" aria-hidden="true"><rect x="1.5" y="3" width="13" height="11" rx="1.5" fill="#24518a"/><rect x="4" y="1" width="7" height="4" fill="#fff" stroke="#24518a"/><rect x="4" y="7" width="8" height="2" fill="#fff"/><rect x="4" y="10.5" width="8" height="1.5" fill="#fff"/></svg>
        <span>(+11) 555 018 2241</span>
      </div>
      <div class="line">
        <svg viewBox="0 0 16 16" aria-hidden="true"><rect x="1" y="3.5" width="14" height="9" fill="#24518a"/><path d="M1 3.5l7 5 7-5" fill="none" stroke="#fff" stroke-width="1.2"/></svg>
        <span>info@verlanbuild.com</span>
      </div>
    </div>

    <div class="web-tab">www.verlanbuild.com</div>
  </section>

</body>
</html>
```